Carpet cleaning company focused on high quality needs business cards

We are a growing company that just merged with another company and need to design a new business card. We do both residential as well as commercial cleaning. We do carpet, tile & grout, upholstery, hard floors, and stain & pet odor removal. We treat our customers like family and strive to achieve outstanding results with every job.

```html
<!DOCTYPE html>
<html lang="en">
<head>
<meta charset="utf-8">
<title>Marlow Steam Crew – Business Card</title>
<link href="https://fonts.googleapis.com/css2?family=Open+Sans:wght@400;600;700;800&display=swap" rel="stylesheet">
<style>
  :root {
    --page-bg: #e9e4dd;
    --card-bg: #f4f1ec;
    --ink: #2f2f2f;
    --ink-soft: #3d3d3d;
    --teal: #2b7791;
    --red: #d8362f;
    --art-blue: #2f7ea0;
    --art-cream: #efe6dc;
  }
  * { box-sizing: border-box; margin: 0; padding: 0; }
  html, body {
    width: 1200px;
    height: 1047px;
    overflow: hidden;
    background: var(--page-bg);
    font-family: "Open Sans", Arial, sans-serif;
    color: var(--ink);
  }
  .business-card {
    position: absolute;
    left: 151px;
    top: 289px;
    width: 948px;
    height: 518px;
    background: var(--card-bg);
    border-radius: 24px;
    overflow: hidden;
    box-shadow: 0 6px 24px rgba(0,0,0,0.12);
  }
  .brand {
    position: absolute;
    left: 40px;
    top: 92px;
    display: flex;
    align-items: center;
    gap: 14px;
  }
  .brand-square {
    width: 48px;
    height: 48px;
    background: var(--red);
    flex: none;
  }
  .brand-name {
    font-size: 26px;
    font-weight: 800;
    line-height: 1.08;
    color: var(--ink);
    width: 200px;
  }
  .name-marker {
    position: absolute;
    left: 0;
    top: 236px;
    width: 27px;
    height: 54px;
    background: var(--red);
  }
  .person-name {
    position: absolute;
    left: 43px;
    top: 228px;
    font-size: 31px;
    font-weight: 600;
    line-height: 1.2;
    white-space: nowrap;
  }
  .person-name .first { color: var(--teal); }
  .person-name .last { color: var(--red); }
  .person-title {
    position: absolute;
    left: 43px;
    top: 270px;
    font-size: 21px;
    line-height: 1.2;
    color: var(--ink-soft);
    white-space: nowrap;
  }
  .contact-list {
    position: absolute;
    left: 43px;
    top: 312px;
    list-style: none;
    font-size: 22px;
    color: var(--ink-soft);
  }
  .contact-list li {
    display: flex;
    align-items: center;
    gap: 6px;
    height: 32px;
    white-space: nowrap;
  }
  .contact-list svg { width: 20px; height: 20px; fill: var(--teal); flex: none; }
  .address {
    position: absolute;
    left: 43px;
    top: 427px;
    font-size: 22px;
    line-height: 31px;
    color: var(--ink-soft);
    white-space: nowrap;
  }
  .illustration-area {
    position: absolute;
    right: 0;
    top: 0;
    width: 463px;
    height: 100%;
    background: linear-gradient(165deg, var(--art-cream) 0%, var(--art-cream) 40%, var(--art-blue) 55%, var(--red) 72%, var(--red) 100%);
    opacity: 0.9;
  }
</style>
</head>
<body>
  <article class="business-card">
    <div class="brand">
      <span class="brand-square"></span>
      <span class="brand-name">Marlow Steam Crew</span>
    </div>

    <span class="name-marker"></span>
    <h1 class="person-name"><span class="first">Dana</span> <span class="last">Whitfield</span></h1>
    <p class="person-title">Executive Director</p>

    <ul class="contact-list">
      <li>
        <svg viewBox="0 0 24 24" aria-hidden="true"><path d="M6.6 10.8a15.1 15.1 0 0 0 6.6 6.6l2.2-2.2a1 1 0 0 1 1-.25 11.4 11.4 0 0 0 3.6.57 1 1 0 0 1 1 1V20a1 1 0 0 1-1 1A17 17 0 0 1 3 4a1 1 0 0 1 1-1h3.5a1 1 0 0 1 1 1c0 1.25.2 2.45.57 3.6a1 1 0 0 1-.25 1z"/></svg>
        123 456 789
      </li>
      <li>
        <svg viewBox="0 0 24 24" aria-hidden="true"><path d="M3 6h18v12H3z"/><path d="M3 6l9 7 9-7" fill="none" stroke="#f4f1ec" stroke-width="1.8"/></svg>
        info@marlowsteam.com
      </li>
      <li>
        <svg viewBox="0 0 24 24" aria-hidden="true"><circle cx="12" cy="12" r="10"/><path d="M2 12h20M12 2c3 3 3 17 0 20M12 2c-3 3-3 17 0 20" fill="none" stroke="#f4f1ec" stroke-width="1.4"/></svg>
        www.marlowsteam.com
      </li>
    </ul>

    <p class="address">1270 Harbor Lane<br>Coral Springs,</p>

    <div class="illustration-area" role="img" aria-label="Space for the company's own brand illustration"></div>
  </article>
</body>
</html>
```